Yoga/movement guide/teacher for adult yoga practice and kid yoga

What is the positioning or mission statement of your company? to guide individuals in a yoga-based safe and sustainable movement practice applicable to all ages and body types. Currently my focus is working with children in daycare and school settings, but my goal is to expand into private yoga practice for adults, and potentially as part of rented space in studios. I hope to find a way to work with children AND adults (so would love for logo to be appealing to both), but current focus is with children based on need and demand in the community. yoga for children also compliments my backround as a pediatrician/neonatologist, and I greatly miss interacting with children. I also want to emphasize a yoga/movement practice that is focused more on what one feels internally through movement. NOT what one looks like asthetically. I believe in removing all mirrors from yoga/movement practice. It should be an experience of movement/poses/yoga through appropriate cueing and education. It is not about the details of how far the knee should bend, or how high the leg should be. Focusing on foudation first, core, then core engagement and ultimately expression of poses/movements. A focus on strength, stability and mobility, not just flexibility, which is the common perception/association with yoga. I also want individuals to learn to be an advocate of their own health. Through guidance, I hope for individuals to connect with their body so they know themselves so well to be able to advocate for themselves in the modern healthcare world. This internal experience and connection is so essential in a world where modern medicine has become a business and it is all about making a dollar. the connection with patients is lost, and individuals need to learn to empower themselves and through their new found voice to be able to articulate what is wrong.<br/>Does your company have a tagline or slogan that should be included with the logo? "Move From Within"<br/>What do you hope your company can be known for? Accessible yoga for a sustained practice. A guided movement practice where one gains information and knowledge of oneself through a mind/body connection. For one feel good physically with a new awaraness of their internal radiance that exists in all beings. Physical rejuvenation egnites a light and increases energy to flow through the physical body, which ultimately tranlates into works of kindness for others and out in the world. <br/>What color palettes might you prefer? why? love the colors currently chosen<br/>Where will the logo be primarily used? initially business cards, but hopefully future websites, t-shirts, and potentially local magazine adds. Also starting with a small couple of banners for community events in the area. I currently practice as a nomad out of my car :)<br/>Are there any elements you would prefer to see in the logo? Movement. A modern depiction of a human body/figure practicing movement. Hoping to avoid a stereotypical yoga pose per say, just because I want to people to think of it more of a movement practice with yoga roots. Modern yoga. There are elements of breathing and connecting with oneself through the flow of breath and movement, but I do not focus on the meditative/cerebral aspect of the yoga practice. What I teach is almost reaching a meditative state through movement. I personally don't practice, nor resonate with just seated meditation. just not my thing :)<br/>In your opinion, what defines a well-designed logo? curiosity. enough info for individuals to think they know what it means, but want to know more. invokes curiosity, but not too abstract. Reproducible. not too complicated. I want also to invoke a community feel, so a design that appeals to all people within a community. <br/>What is your preference in reference to icons, typography, spokespeople (characters), etc.? modern design. I love the idea of a logo for my purposes, to invoke a sense of movement from within. So not too static. <br/>What words or icons must be included in the logo? movement with yoga roots. <br/>What logos do you like and why? A representation, but not exact. I think some ambiguity is intriguing for others, and also memorable. I want it to be an artistic representation of movement/yoga<br/>What logos do you dislike and why? too busy, too loud. <br/>In your opinion, what is the primary purpose for a logo? association<br/>Who is the primary target audience? (who is most likely to use your services/product?) Children and their parents, but ultimately to expand into teaching adults. I even have aspirations of prenatal and post-natal yoga. Potentially incorporating infants. <br/>Who currently uses your product the most? n/a (working in schools/daycare currently. It is currently all volunteer)<br/>Are you pleased with the range of people your company serves? n/a<br/>Are you looking to expand, modify, or completely change your target audience? or will it remain the same? yes! expand into an adult audience. <br/>How do you plan to focus on your target audience? currently by working through schools and daycares. hopefully ultimately through after school care programs and then offering kid yoga in an existing yoga studio (working on this with Q Studio in Ridgeland, currently)<br/>What are your main forms of advertising? word of mouth, schools, daycares. Happy kids talking to their parents about the yoga class they took and happy teachers :)<br/>How do most customers find out about your company?<br/>Which gender are you targeting? All genders! However, with kid yoga, often the maternal individual in the child's life is more involved with decision making as far as extracurricular activities

Target Market(s)

individuals and families interested in wellness and feeling great

Contact Information for Business Card

Dana Whitford
Yoga Instructor
RYT-200, RCYT

certified yoga teacher for adults and children

Colors

Designer to choose colors to be used in the design.

Requirements
Must have
• "Move From Within"
Nice to have
• logo with same colors

```html
<!DOCTYPE html>
<html lang="en">
<head>
<meta charset="utf-8">
<title>Brightfold Studio – Business Card</title>
<link rel="stylesheet" href="https://fonts.googleapis.com/css2?family=Arimo:wght@400&family=Gochi+Hand&display=swap">
<style>
  :root {
    --stage: #2b2b2b;
    --card-white: #ffffff;
    --card-grey: #808281;
    --sun-yellow: #f5d93a;
    --sea-teal: #5ec8d0;
    --ink-grey: #6b6b6b;
  }
  * { box-sizing: border-box; margin: 0; padding: 0; }
  html, body { width: 1200px; height: 900px; overflow: hidden; }
  body {
    background: var(--stage);
    font-family: "Arimo", Arial, sans-serif;
    display: flex; flex-direction: column; align-items: center; justify-content: center;
    gap: 40px;
  }
  .card {
    position: relative;
    width: 700px; height: 400px;
    overflow: hidden;
  }

  /* Back side */
  .card-back { background: var(--card-grey); display: flex; align-items: center; justify-content: center; }
  .card-back .texture {
    position: absolute; inset: 0;
    background: radial-gradient(ellipse at center, #8a8c8b 0%, var(--card-grey) 70%);
  }
  .brand-mark {
    position: relative;
    display: flex; align-items: center; gap: 14px;
  }
  .brand-dot { width: 34px; height: 34px; border-radius: 50%; background: var(--sun-yellow); }
  .brand-name { font-size: 40px; color: var(--sun-yellow); font-weight: 400; }

  /* Front side */
  .card-front { background: var(--card-white); }
  .front-logo { position: absolute; left: 50px; top: 44px; }
  .front-logo .brand-dot { width: 28px; height: 28px; }
  .front-logo .brand-name { font-size: 30px; color: var(--ink-grey); }
  .tagline {
    position: absolute; left: 92px; top: 92px;
    font-size: 9px; letter-spacing: 1.5px; text-transform: uppercase;
    color: var(--sea-teal);
  }
  .accent-tick {
    position: absolute; left: 0; top: 168px;
    width: 6px; height: 46px; background: var(--sea-teal);
  }
  .person-name {
    position: absolute; left: 46px; top: 150px;
    font-family: "Gochi Hand", cursive;
    font-weight: 400;
    font-size: 40px; line-height: 48px; color: var(--sun-yellow);
  }
  .person-role {
    position: absolute; left: 46px; top: 200px;
    font-size: 21px; color: var(--ink-grey);
  }
  .divider {
    position: absolute; left: 46px; right: 50px; top: 240px;
    height: 2px; background: var(--sea-teal);
  }
  .contact-list {
    position: absolute; left: 46px; top: 258px;
    list-style: none;
  }
  .contact-list li {
    display: flex; align-items: center; gap: 10px;
    font-size: 21px; color: var(--ink-grey); line-height: 30px;
  }
  .contact-list svg { width: 20px; height: 20px; flex: none; }
  .band-yellow {
    position: absolute; left: 0; bottom: 0;
    width: 320px; height: 22px; background: var(--sun-yellow);
  }
  .band-teal {
    position: absolute; left: 320px; right: 0; bottom: 0;
    height: 8px; background: var(--sea-teal);
  }
</style>
</head>
<body>

  <section class="card card-back" aria-label="Card back">
    <div class="texture"></div>
    <div class="brand-mark">
      <span class="brand-dot"></span>
      <span class="brand-name">Brightfold Studio</span>
    </div>
  </section>

  <section class="card card-front" aria-label="Card front">
    <div class="front-logo brand-mark">
      <span class="brand-dot"></span>
      <span class="brand-name">Brightfold Studio</span>
    </div>
    <p class="tagline">Move From Within</p>

    <span class="accent-tick"></span>
    <h1 class="person-name">Dana Whitford</h1>
    <p class="person-role">Owner-Operator</p>
    <span class="divider"></span>

    <ul class="contact-list">
      <li>
        <svg viewBox="0 0 20 20" fill="none" stroke="var(--sea-teal)" stroke-width="1.6">
          <circle cx="10" cy="10" r="8.5"/>
          <path d="M7 5.5l1.6 2.6-1 1.2c.7 1.4 1.7 2.4 3.1 3.1l1.2-1 2.6 1.6-.8 1.6c-3.8-.4-7-3.6-7.4-7.4z"/>
        </svg>
        555-014-2270
      </li>
      <li>
        <svg viewBox="0 0 20 20" fill="none" stroke="var(--sea-teal)" stroke-width="1.6">
          <rect x="2" y="4.5" width="16" height="11"/>
          <path d="M2 4.5l8 6.5 8-6.5"/>
        </svg>
        dana.whitford@brightmail.com
      </li>
      <li>
        <svg viewBox="0 0 20 20" fill="none" stroke="var(--sea-teal)" stroke-width="1.6">
          <circle cx="10" cy="10" r="8.5"/>
          <ellipse cx="10" cy="10" rx="3.5" ry="8.5"/>
          <path d="M1.5 10h17M3 6h14M3 14h14"/>
        </svg>
        www.brightfoldstudio.com
      </li>
    </ul>

    <span class="band-yellow"></span>
    <span class="band-teal"></span>
  </section>

</body>
</html>
```